Quote Cards With KB May 2025 for Instagram

I would like to put these quotes over one of the pictures attached; Instagram (new size: 4:5 (1080 x 1350 pixels) One Quote per picture, and I want the quote to be bold or easy to read as well. I provided a few reference graphics that I really like as examples below. In very small letters at the bottom add @KBHarlowOnline

All of the pictures are attached; you can pick any photo and add one quote to it; but no stock photography

```html
<!DOCTYPE html>
<html lang="en">
<head>
<meta charset="utf-8">
<title>KB Quote Card</title>
<link rel="stylesheet" href="https://fonts.googleapis.com/css2?family=Oswald:wght@700&family=Poppins:wght@400&display=swap">
<style>
  :root {
    --ink: #0b1a24;
    --pink: #ec1a8c;
    --pink-soft: #f9b3d8;
    --blush: #fdeef6;
    --white: #ffffff;
    --handle: #2b2b2b;
  }
  html, body {
    margin: 0;
    padding: 0;
    width: 960px;
    height: 1200px;
    overflow: hidden;
  }
  .card {
    position: relative;
    width: 960px;
    height: 1200px;
    overflow: hidden;
    background:
      radial-gradient(ellipse 70% 60% at 42% 45%, var(--white) 0%, var(--blush) 55%, var(--pink-soft) 100%);
  }
  .frame {
    position: absolute;
    left: 18px;
    top: 18px;
    width: 922px;
    height: 1162px;
    border: 2px solid transparent;
    border-image: linear-gradient(135deg, var(--pink) 0%, rgba(236,26,140,0.15) 40%, rgba(236,26,140,0.15) 60%, var(--pink) 100%) 1;
    box-sizing: border-box;
  }
  .portrait {
    position: absolute;
    left: 612px;
    top: 44px;
    width: 300px;
    height: 1078px;
    border-radius: 140px 140px 60px 60px;
    background: linear-gradient(180deg, #3a2a24 0%, #1a1416 25%, #0f0d10 60%, #1b1a1c 100%);
  }
  .quote {
    position: absolute;
    left: 86px;
    top: 172px;
    margin: 0;
    font-family: 'Oswald', sans-serif;
    font-weight: 700;
    font-size: 112px;
    line-height: 116px;
    color: var(--ink);
    text-transform: uppercase;
    letter-spacing: -0.5px;
    white-space: nowrap;
  }
  .quote .line { display: block; }
  .quote .outline {
    color: transparent;
    -webkit-text-stroke: 2px var(--pink);
  }
  .handle {
    position: absolute;
    left: 83px;
    top: 1084px;
    font-family: 'Poppins', sans-serif;
    font-size: 25px;
    color: var(--handle);
  }
</style>
</head>
<body>
  <main class="card">
    <div class="frame"></div>
    <div class="portrait" role="img" aria-label="Full-length photo of KB standing, hand on hip, wearing a sheer black mesh top, black pants and lace-up boots"></div>
    <h1 class="quote">
      <span class="line">Tired. Moo<span class="outline">dy.</span></span>
      <span class="line">Stubborn</span>
      <span class="line">Belly fat. <span class="outline">Your</span></span>
      <span class="line">Hormones <span class="outline">are</span></span>
      <span class="line">Screaming <span class="outline">for</span></span>
      <span class="line">Help! Let’s <span class="outline">fix</span></span>
      <span class="line">That.</span>
    </h1>
    <p class="handle">@KBHarlowOnline</p>
  </main>
</body>
</html>
```